Real estate broker business card

Want a modern celan but effective business card for my residential and commercial real estate business. I want the back of the card to advertise my services and to capture business. I have attached the back of my current business card fore ideas
Updates

Logos, photo and text updates added! Added Saturday, September 3, 2016

Project Deadline Extended Reason: LOGOS, PHOTOS AND TEST JUST UPLOADED! I'M READY TO PICK A DESIGN! THANK YOU! Added Saturday, September 3, 2016

Target Market(s)

home buyers and seller. commercial buyers and sellers

Industry/Entity Type

Real Estate

Contact Information for Business Card

must have my contact information and my photo

Requirements
Must have
• Carla Ventrino
• Owner & Qualifying Broker
• Ventrino Real Estate Services
• 505.718.2094
• carla@ventrinohomes.example
• www.ventrinohomes.example
Nice to have
• metallic
• Business capture text: " Don't buy or lease property without someone looking out for your best interests. I will represent you on your home or investment purchase for FREE!"
• "Home owners, call today to receive a FREE market analysis for your homes value!

```html
<!DOCTYPE html>
<html lang="en">
<head>
<meta charset="utf-8">
<title>Ventrino Real Estate Services – Business Card</title>
<link href="https://fonts.googleapis.com/css2?family=Cinzel:wght@500;600&family=Montserrat:wght@400;500;600&display=swap" rel="stylesheet">
<style>
  :root {
    --backdrop: #e8e9eb;
    --ink: #050505;
    --teal: #1a7f8e;
    --steel-text: #6f7274;
    --label: #111;
    --shadow: rgba(0,0,0,0.28);
  }
  * { margin: 0; padding: 0; box-sizing: border-box; }
  html, body { width: 1200px; height: 1000px; overflow: hidden; background: var(--backdrop); }
  .canvas { position: relative; width: 1200px; height: 1000px; }
  .card { position: absolute; left: 278px; width: 644px; height: 376px; box-shadow: 3px 5px 8px var(--shadow); overflow: hidden; }
  .card--front { top: 120px; }
  .card--back { top: 540px; }
  .card svg.card-art { position: absolute; inset: 0; width: 644px; height: 376px; }

  .brand-name { font-family: "Cinzel", serif; font-weight: 600; color: var(--teal); line-height: 1; }
  .brand-tag { font-family: "Montserrat", sans-serif; color: var(--steel-text); letter-spacing: 2.5px; line-height: 1; }

  .front-brand { position: absolute; top: 215px; left: 0; width: 644px; text-align: center; }
  .front-brand .brand-name { font-size: 46px; letter-spacing: 1px; }
  .front-brand .brand-tag { font-size: 15.5px; margin-top: 6px; font-weight: 400; }
  .front-mark { position: absolute; left: 287px; top: 100px; width: 70px; height: 70px; border-radius: 50%; background: var(--teal); }

  .back-mark { position: absolute; left: 48px; top: 60px; width: 74px; height: 74px; border-radius: 50%; background: var(--teal); }
  .back-brand { position: absolute; left: 136px; top: 74px; }
  .back-brand .brand-name { font-size: 38px; }
  .back-brand .brand-tag { font-size: 12.5px; font-weight: 600; margin-top: 6px; letter-spacing: 1.6px; }

  .agent { position: absolute; left: 62px; top: 172px; }
  .agent-name { font-family: "Cinzel", serif; font-weight: 600; font-size: 30px; color: var(--teal); line-height: 1; }
  .agent-role { font-family: "Montserrat", sans-serif; font-size: 17.5px; color: var(--label); margin-top: 6px; }

  .contact { position: absolute; left: 62px; top: 254px; list-style: none; font-family: "Montserrat", sans-serif; font-size: 15px; color: var(--label); }
  .contact li { display: flex; align-items: center; height: 21.5px; }
  .contact .icon { width: 16px; height: 16px; margin-right: 6px; flex: none; }
</style>
</head>
<body>
<div class="canvas">

  <section class="card card--front">
    <svg class="card-art" viewBox="0 0 644 376" aria-hidden="true">
      <defs>
        <linearGradient id="steel" x1="0" y1="0" x2="1" y2="1">
          <stop offset="0" stop-color="#9a9b9d"/>
          <stop offset="0.3" stop-color="#f4f4f4"/>
          <stop offset="0.55" stop-color="#8d8e90"/>
          <stop offset="0.75" stop-color="#e9e9ea"/>
          <stop offset="1" stop-color="#a5a6a8"/>
        </linearGradient>
        <linearGradient id="rim" x1="0" y1="0" x2="1" y2="0">
          <stop offset="0" stop-color="#555"/>
          <stop offset="0.5" stop-color="#fff"/>
          <stop offset="1" stop-color="#666"/>
        </linearGradient>
      </defs>
      <rect width="644" height="376" fill="url(#steel)"/>
      <path class="black-band" d="M0,112 C90,60 180,42 330,42 L540,42 C600,42 630,25 644,8 L644,262 C615,305 560,328 420,330 L240,330 C120,330 40,340 0,362 Z" fill="var(--ink)"/>
      <path d="M0,106 C90,54 180,36 330,36 L540,36 C600,36 630,19 644,2" fill="none" stroke="url(#rim)" stroke-width="5"/>
      <path d="M644,268 C615,311 560,334 420,336 L240,336 C120,336 40,346 0,368" fill="none" stroke="url(#rim)" stroke-width="5"/>
    </svg>
    <div class="front-mark"></div>
    <div class="front-brand">
      <div class="brand-name">VENTRINO</div>
      <div class="brand-tag">REAL ESTATE SERVICES</div>
    </div>
  </section>

  <section class="card card--back">
    <svg class="card-art" viewBox="0 0 644 376" aria-hidden="true">
      <defs>
        <linearGradient id="steel2" x1="0" y1="0" x2="1" y2="1">
          <stop offset="0" stop-color="#d9d9da"/>
          <stop offset="0.4" stop-color="#f5f5f5"/>
          <stop offset="0.7" stop-color="#a9aaac"/>
          <stop offset="1" stop-color="#d0d0d1"/>
        </linearGradient>
        <linearGradient id="nameband" x1="0" y1="0" x2="0" y2="1">
          <stop offset="0" stop-color="#8e8f91"/>
          <stop offset="0.25" stop-color="#fafafa"/>
          <stop offset="0.7" stop-color="#d4d4d5"/>
          <stop offset="1" stop-color="#6e6f71"/>
        </linearGradient>
        <linearGradient id="photoTone" x1="0" y1="0" x2="0" y2="1">
          <stop offset="0" stop-color="#2f4a2a"/>
          <stop offset="0.45" stop-color="#3a2b24"/>
          <stop offset="1" stop-color="#cfc9c4"/>
        </linearGradient>
        <linearGradient id="rim2" x1="0" y1="0" x2="1" y2="0">
          <stop offset="0" stop-color="#444"/>
          <stop offset="0.5" stop-color="#fff"/>
          <stop offset="1" stop-color="#555"/>
        </linearGradient>
      </defs>
      <rect width="644" height="376" fill="url(#steel2)"/>
      <rect width="374" height="162" fill="var(--ink)"/>
      <rect y="162" width="374" height="80" fill="url(#nameband)"/>
      <rect x="374" width="270" height="330" fill="url(#photoTone)" role="img" aria-label="Portrait photo of Carla Ventrino"/>
      <path d="M0,336 C150,318 440,334 644,288 L644,376 L0,376 Z" fill="url(#steel2)"/>
      <path d="M0,336 C150,318 440,334 644,288" fill="none" stroke="url(#rim2)" stroke-width="5"/>
    </svg>
    <div class="back-mark"></div>
    <div class="back-brand">
      <div class="brand-name">VENTRINO</div>
      <div class="brand-tag">REAL ESTATE SERVICES</div>
    </div>
    <div class="agent">
      <div class="agent-name">CARLA VENTRINO</div>
      <div class="agent-role">Owner &amp; Qualifying Broker</div>
    </div>
    <ul class="contact">
      <li><svg class="icon" viewBox="0 0 16 16"><circle cx="8" cy="8" r="8" fill="var(--teal)"/><path d="M5 11 L11 5" stroke="#fff" stroke-width="2" stroke-linecap="round"/></svg>505.718.2094</li>
      <li><svg class="icon" viewBox="0 0 16 16"><circle cx="8" cy="8" r="8" fill="var(--teal)"/><rect x="4" y="5.5" width="8" height="5.5" fill="#fff"/><path d="M4 5.5 L8 8.5 L12 5.5" fill="none" stroke="var(--teal)" stroke-width="1"/></svg>carla@ventrinohomes.example</li>
      <li><svg class="icon" viewBox="0 0 16 16"><circle cx="8" cy="8" r="8" fill="var(--teal)"/><path d="M4 5 L5.8 11 L8 6.5 L10.2 11 L12 5" fill="none" stroke="#fff" stroke-width="1.4"/></svg>www.ventrinohomes.example</li>
    </ul>
  </section>

</div>
</body>
</html>
```